New Business Card Design for Manufacturing

We are an engineering/manufacturing company that offers Advanced machining/assembly/engineering services, as well as innovative products for the heavy duty engine cooling markets.

We are looking to get a new business card designed that is clean and modern looking, but still fits the wide range of technical/skilled work we do.

- We hope to use this design as the base for other design work in new Presentations, web, and print work.

Industry/Entity Type

Engineering

Contact Information for Business Card

Our preferred color of blue is (RGB) 22/71/159 but can vary slightly from that color. Our content will be our Logo and full company name (Vantrell Forge Works, Inc.), company address, name, job title, phone number with extension, cell number, fax number, website, and email address on the cards.
We'd like the full company name next to the logo, but we are open to other interpretations of that layout.
Preferably, we would like the back side to be clean with just our logo, and the front to contain all of the contact information.

Colors
2f74b4
0355a3
85abd2

Requirements
Must have
• - Logo, company name, needed content - We are open to interpretation beyond that.
• - Standard size business card.
• - Horizontal orientation.
• - Enough space for lengthy names / job titles (for example, a job title could read "Directory of Human Resources" or "V.P. of Governmental Affairs"). We need this to look clean, whether the title be short (CEO) or long (as described above).

```html
<!DOCTYPE html>
<html lang="en">
<head>
<meta charset="utf-8">
<title>Vantrell Forge Works — Business Card</title>
<link href="https://fonts.googleapis.com/css2?family=Exo+2:wght@400;500;600;700;800&display=swap" rel="stylesheet">
<style>
  :root {
    --brand-blue: #0355a3;
    --brand-mid: #2f74b4;
    --brand-light: #85abd2;
    --ink: #3a3d42;
    --paper: #ffffff;
    --backdrop: #eceef1;
  }
  * { box-sizing: border-box; margin: 0; padding: 0; }
  html, body {
    width: 1200px; height: 800px; overflow: hidden;
    background: var(--backdrop);
    font-family: "Exo 2", sans-serif;
  }
  .canvas { position: relative; width: 1200px; height: 800px; }

  .card {
    position: absolute; width: 540px; height: 310px;
    box-shadow: 0 6px 18px rgba(0,0,0,.18);
    overflow: hidden;
  }

  /* Back side */
  .card-back { left: 60px; top: 110px; background: var(--brand-blue); color: var(--paper); }
  .back-lockup {
    position: absolute; left: 0; right: 0; top: 50%;
    transform: translateY(-50%);
    display: flex; align-items: center; justify-content: center; gap: 22px;
  }
  .back-wordmark { font-weight: 800; font-size: 54px; letter-spacing: 1px; line-height: 1; }
  .back-company {
    font-weight: 800; font-size: 19px; line-height: 1.02;
    text-transform: uppercase; letter-spacing: .5px;
  }
  .back-company small { font-size: 10px; vertical-align: top; }

  /* Front side */
  .card-front { left: 600px; top: 370px; background: var(--paper); color: var(--ink); }
  .holder { position: absolute; left: 28px; top: 26px; }
  .holder-name { color: var(--brand-blue); font-weight: 700; font-size: 18px; letter-spacing: .5px; }
  .holder-title { font-size: 17px; font-weight: 400; color: var(--ink); margin-top: 1px; }

  .phones { position: absolute; left: 28px; top: 112px; list-style: none; }
  .phones li { display: flex; align-items: center; gap: 10px; font-size: 14px; line-height: 22px; }
  .phones svg { width: 13px; height: 13px; fill: var(--brand-blue); }

  .front-wordmark {
    position: absolute; right: 30px; top: 106px;
    color: var(--brand-blue); font-weight: 800; font-size: 40px; line-height: 1;
  }

  .online { position: absolute; right: 28px; top: 178px; list-style: none; text-align: right; }
  .online li { display: flex; justify-content: flex-end; align-items: center; gap: 10px; font-size: 14px; line-height: 22px; }
  .online svg { width: 13px; height: 13px; fill: var(--brand-blue); }

  .band { position: absolute; left: 0; bottom: 0; width: 540px; height: 310px; }
  .band-name {
    position: absolute; left: 28px; top: 260px;
    color: var(--paper); font-weight: 600; font-size: 13.5px;
    text-transform: uppercase; letter-spacing: .3px;
  }
  .address {
    position: absolute; right: 28px; top: 248px; text-align: right;
    font-size: 13px; line-height: 17px;
  }
</style>
</head>
<body>
<main class="canvas">

  <section class="card card-back" aria-label="Card back">
    <div class="back-lockup">
      <span class="back-wordmark">Vantrell</span>
      <span class="back-company">Vantrell<br>Forge<br>Works <small>INC</small></span>
    </div>
  </section>

  <section class="card card-front" aria-label="Card front">
    <svg class="band" viewBox="0 0 540 310" aria-hidden="true">
      <path d="M0 245 H255 Q282 245 292 268 Q302 292 330 292 H540 V310 H0 Z" fill="var(--brand-blue)"/>
    </svg>

    <div class="holder">
      <p class="holder-name">MARCUS ELLERY</p>
      <p class="holder-title">Directory of Human Resources</p>
    </div>

    <ul class="phones">
      <li><svg viewBox="0 0 16 16"><path d="M4 0h8a1 1 0 0 1 1 1v14a1 1 0 0 1-1 1H4a1 1 0 0 1-1-1V1a1 1 0 0 1 1-1zm0 2v11h8V2z"/></svg>555-014-2290</li>
      <li><svg viewBox="0 0 16 16"><path d="M3.6 1l2.3 3.2-1.4 1.6a9 9 0 0 0 5.7 5.7l1.6-1.4L15 12.4 13.5 15C6.5 14.5 1.5 9.5 1 2.5z"/></svg>555-014-2291 x204</li>
      <li><svg viewBox="0 0 16 16"><path d="M4 1h7l1 2v3h2a1 1 0 0 1 1 1v7a1 1 0 0 1-1 1H2a1 1 0 0 1-1-1V7a1 1 0 0 1 1-1h2zm1 1v4h6V3.5L10.5 2zM4 10v2h8v-2z"/></svg>555-014-2292</li>
    </ul>

    <p class="front-wordmark">Vantrell</p>

    <ul class="online">
      <li>m.ellery@vantrellforge.com<svg viewBox="0 0 16 16"><path d="M1 3h14v10H1zm1.5 1.2L8 8.5l5.5-4.3z"/></svg></li>
      <li>www.vantrellforge.com<svg viewBox="0 0 16 16"><path d="M8 1a7 7 0 1 0 0 14A7 7 0 0 0 8 1zm0 1.5c.8 0 1.7 1.6 2 4H6c.3-2.4 1.2-4 2-4zM2.6 7.5h2.4c0-1 .2-2 .5-3a5.5 5.5 0 0 0-2.9 3zm8.4 0h2.4a5.5 5.5 0 0 0-2.9-3c.3 1 .5 2 .5 3zM2.6 8.5a5.5 5.5 0 0 0 2.9 3c-.3-1-.5-2-.5-3zm3.4 0c.1 2.5 1.2 4 2 4s1.9-1.5 2-4zm5 0c0 1-.2 2-.5 3a5.5 5.5 0 0 0 2.9-3z"/></svg></li>
    </ul>

    <p class="band-name">Vantrell Forge Works</p>
    <p class="address">418 Calder Row<br>Brenton, MA 01942</p>
  </section>

</main>
</body>
</html>
```